Certificates with Watermark Images

We are looking for a design of One page Certificates with Watermark (background) images where text will be printed over it .
Graphics design is required to reflect the flowing categories:
IPTV (Internet Protocol TV)
VoD (Video on Demand)
Satellite Receiver
Graphics design images for all three categories must be provided to maintain the same them .
Thank you and good luck.
Industry/Entity Type
Internet
Requirements
Must have
- Graphics design images for all three categories must be provided to maintain the same them

```html
<!DOCTYPE html>
<html lang="en">
<head>
<meta charset="utf-8">
<title>Certificate – Nova Metro Satellite Service</title>
<link rel="stylesheet" href="https://fonts.googleapis.com/css2?family=Fira+Sans:ital,wght@0,400;0,500;0,700;1,700&display=swap">
<style>
  :root {
    --page-bg: #ffffff;
    --frame-line: #3a3a3a;
    --ink: #222428;
    --accent-blue: #1e9be0;
    --sky-light: #e6f3fc;
    --sky-mid: #b9dcf4;
    --sky-deep: #8cc3ea;
    --globe-land: #b7b2ad;
    --logo-orange: #ef5a24;
    --seal-blue: #2a12a8;
    --signature-tint: #d7dcf3;
  }

  * { margin: 0; padding: 0; box-sizing: border-box; }

  html, body {
    width: 1200px;
    height: 845px;
    overflow: hidden;
    background: var(--page-bg);
  }

  .certificate {
    position: relative;
    width: 1200px;
    height: 845px;
    font-family: "Fira Sans", Arial, sans-serif;
    color: var(--ink);
  }

  .certificate__frame {
    position: absolute;
    left: 29px;
    top: 29px;
    width: 1152px;
    height: 779px;
    border: 2px solid var(--frame-line);
    border-radius: 48px;
    overflow: hidden;
    background: linear-gradient(100deg, var(--page-bg) 18%, var(--sky-light) 42%, var(--sky-mid) 72%, var(--sky-light) 100%);
  }

  .certificate__backdrop {
    position: absolute;
    inset: 0;
    width: 100%;
    height: 100%;
  }

  .certificate__body {
    position: absolute;
    left: 341px;
    top: 0;
    transform: translateX(-50%);
    width: 460px;
    text-align: center;
  }

  .brand {
    position: absolute;
    left: 50%;
    top: 80px;
    transform: translateX(-50%);
    display: flex;
    flex-direction: column;
    align-items: center;
  }

  .brand__mark {
    width: 66px;
    height: 66px;
    border-radius: 50%;
    background: var(--logo-orange);
  }

  .brand__name {
    margin-top: 14px;
    font-size: 25px;
    font-weight: 500;
    white-space: nowrap;
  }

  .certificate__title {
    position: absolute;
    left: 0; right: 0;
    top: 238px;
    font-size: 43px;
    font-weight: 700;
    letter-spacing: 7px;
  }

  .certificate__intro {
    position: absolute;
    left: 0; right: 0;
    top: 303px;
    font-size: 22px;
  }

  .recipient__name {
    position: absolute;
    left: 0; right: 0;
    top: 334px;
    font-size: 41px;
    font-weight: 500;
    color: var(--accent-blue);
  }

  .recipient__service {
    position: absolute;
    left: 0; right: 0;
    top: 399px;
    font-size: 20px;
  }

  .certificate__citation {
    position: absolute;
    left: 40px; right: 40px;
    top: 441px;
    font-size: 19.5px;
    line-height: 27px;
  }

  .certificate__value {
    position: absolute;
    left: 0; right: 0;
    top: 554px;
    font-size: 20px;
    font-weight: 700;
  }

  .issue-details {
    position: absolute;
    left: 102px;
    top: 652px;
    font-size: 13.5px;
    font-weight: 700;
    font-style: italic;
    line-height: 18px;
  }

  .issue-details__number { margin-bottom: 18px; }
  .issue-details__date { margin-bottom: 16px; }

  .signature {
    position: absolute;
    left: 300px;
    top: 660px;
    width: 90px;
    height: 84px;
  }

  .seal {
    position: absolute;
    left: 485px;
    top: 634px;
    width: 134px;
    height: 134px;
  }
</style>
</head>
<body>
  <main class="certificate">
    <div class="certificate__frame">
      <svg class="certificate__backdrop" viewBox="0 0 1152 779" role="img" aria-label="Faint globe with world map and glowing network light rays">
        <defs>
          <radialGradient id="globe-glow" cx="0.45" cy="0.4" r="0.6">
            <stop offset="0" stop-color="#ffffff" stop-opacity="0.9"/>
            <stop offset="0.35" stop-color="#cfe7f8" stop-opacity="0.8"/>
            <stop offset="0.8" stop-color="#8cc3ea" stop-opacity="0.55"/>
            <stop offset="1" stop-color="#8cc3ea" stop-opacity="0"/>
          </radialGradient>
          <radialGradient id="land-haze" cx="0.5" cy="0.5" r="0.5">
            <stop offset="0" stop-color="#b7b2ad" stop-opacity="0.35"/>
            <stop offset="1" stop-color="#b7b2ad" stop-opacity="0"/>
          </radialGradient>
        </defs>
        <circle cx="825" cy="320" r="420" fill="url(#globe-glow)"/>
        <ellipse cx="900" cy="360" rx="230" ry="260" fill="url(#land-haze)"/>
      </svg>
    </div>

    <section class="certificate__body">
      <div class="brand">
        <span class="brand__mark" aria-hidden="true"></span>
        <span class="brand__name">Our Organization</span>
      </div>

      <h1 class="certificate__title">CERTIFICATE</h1>
      <p class="certificate__intro">this certificate that</p>
      <h2 class="recipient__name">Nova Metro</h2>
      <p class="recipient__service">(satellite service)</p>
      <p class="certificate__citation">has been awarded for his labor achievements and many years of diligent work, also for his labor achievements and many years of diligent work.</p>
      <p class="certificate__value">and has passed for this Certificate $100</p>
    </section>

    <footer class="issue-details">
      <p class="issue-details__number">Certificate No. 0000/1</p>
      <p class="issue-details__date">11 November 2011<br>New-York</p>
      <p class="issue-details__signatory">Our company Genera Director<br>Samir Haddad</p>
    </footer>

    <svg class="signature" viewBox="0 0 90 84" role="img" aria-label="Director's handwritten signature">
      <ellipse cx="45" cy="42" rx="40" ry="34" fill="var(--signature-tint)" opacity="0.6"/>
    </svg>

    <svg class="seal" viewBox="0 0 134 134" role="img" aria-label="Official seal">
      <circle cx="67" cy="67" r="64" fill="var(--seal-blue)"/>
    </svg>
  </main>
</body>
</html>
```